Detail Shop Business card design

i need a business card design for my new detailing company called 'Brisk's Polish Works'. i want an all black and white design . simple, direct and to the point. i want the designer to choose a fitting font to match the logothe front should have logo, address, phone and email and the back side should have a slogan and text indicating that we offer services on anything including cars, trucks, motorcycles and RVs. slogan will read "we take pride in your ride"
maybe also very small on the back side the IG icon with Brisks_Polish_Works

phone 208.417.6352
address 3847 E Larkin Ave
Spokane WA 99214
email: BrisksPolish@mailvexo.com

Target Market(s)

all ages , auto enthusiasts

Industry/Entity Type

Automotive

Contact Information for Business Card

the front should have logo, address, phone and email and the back side should have a slogan and text indicating that we offer services on anything including cars, trucks, motorcycles and RVs. slogan will read "we take pride in your ride"

phone 208.417.6352
address 3847 E Larkin Ave
Spokane WA 99214

Colors
000000
ffffff

Requirements
Must have
• bold font and very simple design with good spacing
Nice to have
• anything creative from the designer indicating we service any types of vehicles
Should not have
• any colors ,

```html
<!DOCTYPE html>
<html lang="en">
<head>
<meta charset="utf-8">
<title>Brisk's Polish Works – Business Card</title>
<link rel="stylesheet" href="https://fonts.googleapis.com/css2?family=Bitter:wght@400;600;700&display=swap">
<style>
  :root {
    --backdrop: #1c1c1c;
    --card: #111111;
    --card-edge: #2a2a2a;
    --ink: #ffffff;
    --ink-soft: #e6e6e6;
  }
  * { margin: 0; padding: 0; box-sizing: border-box; }
  html, body {
    width: 1200px; height: 900px; overflow: hidden;
    background: var(--backdrop);
    font-family: "Bitter", Georgia, serif;
    color: var(--ink);
  }
  .canvas {
    width: 1200px; height: 900px;
    display: flex; flex-direction: column;
    align-items: center; justify-content: center; gap: 40px;
  }
  .card {
    position: relative;
    width: 630px; height: 360px;
    background: linear-gradient(135deg, #181818 0%, var(--card) 60%, #0b0b0b 100%);
    border: 1px solid var(--card-edge);
  }

  /* wordmark stand-in */
  .wordmark {
    display: flex; align-items: center; gap: 14px;
  }
  .wordmark-dot {
    width: 34px; height: 34px; border-radius: 50%;
    border: 3px solid var(--ink); flex: none;
  }
  .wordmark-name {
    font-weight: 700; color: var(--ink);
    text-transform: uppercase; letter-spacing: 1px; line-height: 1.15;
  }

  /* back side */
  .card-back .wordmark {
    position: absolute; left: 50%; top: 120px; transform: translateX(-50%);
  }
  .card-back .wordmark-name { font-size: 30px; white-space: nowrap; }
  .services {
    position: absolute; left: 0; right: 0; bottom: 48px;
    text-align: center; font-size: 16px; font-weight: 600;
    letter-spacing: 1.5px; color: var(--ink-soft);
  }

  /* front side */
  .card-front .wordmark {
    position: absolute; left: 48px; top: 110px; width: 210px;
  }
  .card-front .wordmark-name { font-size: 24px; }
  .divider {
    position: absolute; left: 288px; top: 92px;
    width: 2px; height: 162px; background: var(--ink);
  }
  .contact {
    position: absolute; left: 320px; top: 92px;
  }
  .contact-name {
    font-size: 24px; font-weight: 600; letter-spacing: 1.5px; text-transform: uppercase;
  }
  .contact-role { font-size: 14px; margin-top: 2px; color: var(--ink-soft); }
  .contact-address { font-size: 15px; margin-top: 14px; line-height: 1.35; color: var(--ink-soft); }
  .contact-lines { list-style: none; margin-top: 12px; font-size: 15px; line-height: 1.4; }
  .contact-lines li { display: flex; align-items: center; gap: 10px; }
  .contact-lines svg { width: 11px; height: 11px; flex: none; }
  .slogan {
    position: absolute; left: 0; right: 0; bottom: 34px;
    text-align: center; font-size: 18px; font-weight: 600;
    letter-spacing: 1px; text-transform: uppercase;
  }
</style>
</head>
<body>
<main class="canvas">

  <section class="card card-back" aria-label="Card back">
    <div class="wordmark">
      <span class="wordmark-dot"></span>
      <span class="wordmark-name">Brisk's Polish Works</span>
    </div>
    <p class="services">CARS - TRUCKS - MOTORCYCLES AND RVS</p>
  </section>

  <section class="card card-front" aria-label="Card front">
    <div class="wordmark">
      <span class="wordmark-dot"></span>
      <span class="wordmark-name">Brisk's<br>Polish Works</span>
    </div>
    <div class="divider"></div>
    <div class="contact">
      <h1 class="contact-name">Daniel Reyes</h1>
      <p class="contact-role">Director</p>
      <p class="contact-address">3847 E Larkin Ave<br>Spokane WA 99214</p>
      <ul class="contact-lines">
        <li>
          <svg viewBox="0 0 12 12" aria-hidden="true"><path d="M2.5 1 L4.5 1 L5.2 3.5 L4 4.6 Q5 6.8 7.4 8 L8.5 6.8 L11 7.5 L11 9.5 Q10.5 11 9 11 Q1 10 1 2.5 Q1 1.3 2.5 1 Z" fill="#fff"/></svg>
          208.417.6352
        </li>
        <li>
          <svg viewBox="0 0 12 12" aria-hidden="true"><rect x="0.8" y="2.2" width="10.4" height="7.6" fill="none" stroke="#fff" stroke-width="1.2"/><path d="M1 2.5 L6 6.5 L11 2.5" fill="none" stroke="#fff" stroke-width="1.2"/></svg>
          BrisksPolish@mailvexo.com
        </li>
        <li>
          <svg viewBox="0 0 12 12" aria-hidden="true"><circle cx="6" cy="6" r="5" fill="none" stroke="#fff" stroke-width="1.1"/><ellipse cx="6" cy="6" rx="2.2" ry="5" fill="none" stroke="#fff" stroke-width="1"/><path d="M1 6 H11" stroke="#fff" stroke-width="1"/></svg>
          www.BrisksPolish.com
        </li>
      </ul>
    </div>
    <p class="slogan">We take pride in your ride</p>
  </section>

</main>
</body>
</html>
```